My Pebble Porch Path Blog Re-Do Launch

I need a blog makeover. Someone started for me and they sold their company. The blog is primarily spiritual/inspirational. I would eventually like to monetize and launch some ebooks and/or other products. I am open to suggestions. I am learning as we go along, so please keep that in mind. The final design should be warm and welcoming. I am open to suggestions. I am looking to build a relationship.

Target Market(s)

women, moms, females with chronic health issues, moms of special needs kids, those who need encouragement

Industry/Entity Type

Religious

Number of Pages Required

4 page

Font styles to use
Sans Serif

Colors
eddcec
fdf9cf
ffffff

Requirements
Must have
• I would like my main page to have a short about section, relevant posts, recent posts, and archive posts. The main page should also have a place to subscribe as well a search feature.
Nice to have
• Buttons (grab my button), blogs I follow, e-cart capabilities

```html
<!DOCTYPE html>
<html lang="en">
<head>
<meta charset="utf-8">
<title>My Pebble Porch Path</title>
<link href="https://fonts.googleapis.com/css2?family=Roboto:wght@300;400;500;700&family=Open+Sans:wght@400;600&display=swap" rel="stylesheet">
<style>
:root{
  --ink:#333333;
  --muted:#6b6b6b;
  --dark:#3b3b3b;
  --bar:#404040;
  --blush:#eddcec;
  --cream:#fdf9cf;
  --white:#ffffff;
  --line:#e4e4e4;
  --panel:#eeeeee;
  --gold:#c9a25a;
  --footer:#1c1a18;
}
*{margin:0;padding:0;box-sizing:border-box}
html,body{width:670px;height:1200px;overflow:hidden;background:var(--white)}
body{position:relative;font-family:"Open Sans",Arial,sans-serif;color:var(--ink)}
.abs{position:absolute}
.topbar{left:0;top:0;width:670px;height:24px;background:var(--bar)}
.topbar .divider{left:364px;top:0;width:1px;height:24px;background:#555}
.topbar .phone{left:380px;top:6px;font-size:8px;color:#eee;display:flex;align-items:center;gap:5px}
.topbar .socials{left:514px;top:8px;display:flex;gap:5px}
.topbar .socials span{width:7px;height:7px;background:#ddd;border-radius:1px;display:block}
.topbar .search{left:584px;top:0;width:30px;height:24px;background:var(--white);display:flex;align-items:center;justify-content:center}
.header{left:0;top:24px;width:670px;height:42px;background:var(--white);border-bottom:1px solid var(--line)}
.brand{left:54px;top:6px;display:flex;align-items:center;gap:7px}
.brand .mark{width:30px;height:30px;background:var(--gold)}
.brand .name{font-family:"Roboto",sans-serif;font-weight:500;font-size:12px;line-height:13px;color:var(--dark);text-transform:uppercase;letter-spacing:.3px}
.nav{top:42px;left:0;width:670px;font-family:"Roboto",sans-serif;font-size:7px;color:var(--dark);text-transform:uppercase}
.nav span{position:absolute}
.hero{left:0;top:67px;width:670px;height:283px;background:radial-gradient(circle at 62% 28%,#fff4cf 0%,#e2b86e 30%,#a47a38 65%,#6a5030 100%)}
.hero-caption{left:55px;top:277px;width:560px;height:73px;background:rgba(40,34,26,.72);color:var(--white)}
.hero-caption h1{position:absolute;left:22px;top:14px;font-family:"Roboto",sans-serif;font-weight:500;font-size:17px;letter-spacing:.2px}
.hero-caption p{position:absolute;left:22px;top:39px;width:470px;font-size:7.2px;line-height:11px}
.hero-caption .arrows{position:absolute;right:14px;top:28px}
.section-title{font-family:"Roboto",sans-serif;font-weight:300;font-size:15px;color:var(--ink);display:flex;align-items:center;gap:12px}
.section-title::after{content:"";flex:1;border-top:3px double var(--line)}
.post{left:55px;width:376px;height:107px}
.post .date{position:absolute;left:0;top:0;width:44px;height:52px;background:var(--blush);font-family:"Roboto",sans-serif;font-size:12px;line-height:16px;text-align:center;padding-top:9px;color:var(--dark)}
.post .shares{position:absolute;left:0;top:52px;width:44px;height:55px;border:1px solid var(--line);display:grid;grid-template-columns:1fr 1fr}
.post .shares i{border:1px solid #f0f0f0;display:flex;align-items:center;justify-content:center}
.post .shares i b{width:7px;height:7px;background:#888;border-radius:1px;display:block}
.post .photo{position:absolute;left:51px;top:0;width:123px;height:107px}
.post .card{position:absolute;left:180px;top:0;width:196px;height:107px;border:1px solid var(--line);padding:9px 10px}
.card h3{font-family:"Roboto",sans-serif;font-weight:400;font-size:9.6px;color:var(--dark);margin-bottom:9px;white-space:nowrap;overflow:hidden}
.card .meta{font-size:6.6px;color:#555;margin-bottom:8px}
.card p{font-size:6px;line-height:11.5px;color:#666}
.card .more{font-size:6.4px;color:var(--dark);text-decoration:underline;margin-top:7px;display:block}
.search-panel{left:449px;top:409px;width:167px;height:151px;background:var(--panel);padding:12px 13px}
.search-panel .field{height:21px;background:var(--white);border:1px solid #e2e2e2;margin-bottom:6px;font-size:5.6px;color:#999;padding:7px 8px}
.btn{background:var(--dark);color:var(--white);font-size:6.4px;display:inline-block;text-transform:uppercase}
.search-panel .btn{padding:6px 12px;margin-top:2px;border-radius:2px}
.subscribe{left:449px;top:569px;width:167px;height:71px;background:var(--blush);border:1px solid #ddd}
.subscribe h4{position:absolute;left:45px;top:11px;font-family:"Roboto",sans-serif;font-weight:400;font-size:8.5px;line-height:14px;color:var(--dark);text-transform:uppercase}
.subscribe .email{position:absolute;left:13px;top:42px;width:97px;height:19px;background:var(--white);font-size:5.8px;color:#888;padding:6px 7px}
.subscribe .btn{position:absolute;left:110px;top:42px;width:46px;height:19px;text-align:center;padding-top:6px}
.rel{top:702px;width:128px;height:174px;border:1px solid var(--line)}
.rel .photo{height:90px}
.rel .date{font-family:"Roboto",sans-serif;font-weight:400;font-size:7.6px;color:var(--dark);padding:9px 8px 5px}
.rel p{font-size:5.8px;line-height:10.5px;color:#666;padding:0 8px}
.rel .loc{position:absolute;left:0;bottom:0;width:100%;height:20px;border-top:1px solid var(--line);font-size:5.8px;color:#555;display:flex;align-items:center;padding-left:6px;gap:4px;white-space:nowrap}
.rel .loc .go{position:absolute;right:0;top:0;width:22px;height:19px;border-left:1px solid var(--line);display:flex;align-items:center;justify-content:center;color:#aaa;font-size:7px}
.archive{left:54px;top:912px;width:168px}
.archive h2{font-family:"Roboto",sans-serif;font-weight:400;font-size:13.5px;color:var(--ink);padding-bottom:8px;border-bottom:1px solid var(--line)}
.archive .item{padding:10px 0 9px;border-bottom:1px dotted #ccc}
.archive h3{font-family:"Roboto",sans-serif;font-weight:400;font-size:8px;color:var(--dark);margin-bottom:5px}
.archive .meta{font-size:8px;color:#999;margin-bottom:6px}
.archive .meta small{font-size:5.4px;color:#777}
.archive p{font-size:5.8px;line-height:10.5px;color:#666}
.video{left:244px;top:912px;width:183px;height:178px;border:1px solid var(--line)}
.video .photo{height:117px;background:linear-gradient(135deg,#6d6660,#b79a86 50%,#3d3935)}
.video .play{position:absolute;left:80px;top:46px}
.video h4{font-family:"Roboto",sans-serif;font-weight:300;font-size:10px;text-align:center;margin:7px 0 5px;color:var(--dark)}
.video p{font-size:5.8px;line-height:10.5px;color:#666;text-align:center;padding:0 10px}
.feed{left:455px;top:912px;width:161px;height:178px;border:1px solid var(--line);overflow:hidden}
.feed .head{height:29px;border-bottom:1px solid var(--line);padding:11px 8px;font-family:"Roboto",sans-serif;font-size:8px;color:#2c4a66;text-transform:uppercase}
.feed .badge{position:absolute;left:113px;top:11px;width:28px;height:8px;background:#dfe8f2;border-radius:2px}
.feed .scroll{position:absolute;right:0;top:0;width:6px;height:100%;background:#f2f2f2}
.feed .scroll i{position:absolute;left:1px;top:30px;width:4px;height:60px;background:#bbb;display:block}
.tweet{height:76px;border-bottom:1px solid var(--line);padding:10px 8px;position:relative}
.tweet .av{position:absolute;left:10px;top:10px;width:14px;height:14px;background:var(--cream)}
.tweet .who{margin-left:26px;font-size:6.4px;color:var(--dark);line-height:9px}
.tweet .who small{font-size:5.4px;color:#555;display:block}
.tweet p{font-size:5.6px;line-height:10px;color:#666;margin-top:7px}
.footer{left:0;top:1118px;width:670px;height:82px;background:var(--footer);color:#eee;text-align:center}
.footer .icons{display:flex;justify-content:center;gap:7px;padding-top:14px}
.footer .icons span{width:12px;height:12px;background:#eee;border-radius:2px;display:block}
.footer nav{font-family:"Roboto",sans-serif;font-size:8.6px;margin-top:9px;color:#ddd}
.footer small{display:block;font-size:6.2px;margin-top:8px;color:#ccc}
</style>
</head>
<body>

<div class="abs topbar">
  <div class="abs divider"></div>
  <div class="abs phone">
    <svg width="8" height="8" viewBox="0 0 24 24"><path fill="#eee" d="M6.6 10.8a15 15 0 006.6 6.6l2.2-2.2c.3-.3.7-.4 1-.2 1.1.4 2.3.6 3.6.6.6 0 1 .4 1 1V20c0 .6-.4 1-1 1A17 17 0 013 4c0-.6.4-1 1-1h3.5c.6 0 1 .4 1 1 0 1.3.2 2.5.6 3.6.1.3 0 .7-.2 1z"/></svg>
    Call Us : +1 555 - 014 - 2290
  </div>
  <div class="abs socials"><span></span><span></span><span></span><span></span><span></span></div>
  <div class="abs search">
    <svg width="9" height="9" viewBox="0 0 24 24"><circle cx="10" cy="10" r="6.5" fill="none" stroke="#444" stroke-width="3"/><path d="M15 15l6 6" stroke="#444" stroke-width="3"/></svg>
  </div>
</div>

<header class="abs header">
  <div class="abs brand"><span class="mark"></span><span class="name">My Pebble<br>Porch Path</span></div>
</header>
<nav class="abs nav">
  <span style="left:237px">Home</span>
  <span style="left:284px">Spiritual</span>
  <span style="left:349px">Events</span>
  <span style="left:402px">Recent Posts</span>
  <span style="left:480px">E-Cart Capabilities</span>
  <span style="left:578px">Subscribe</span>
</nav>

<div class="abs hero" role="img" aria-label="Wooden cross against a golden sunlit cloudy sky"></div>
<div class="abs hero-caption">
  <h1>MY PEBBLE PORCH PATH</h1>
  <p>Lorem ipsum dolor sit amet, consectetur adipiscing elit, sed do eiusmod tempor incididunt ut labore et dolore magna aliqua. Ut enim ad minim veniam, quis nostrud exercitation ullamco laboris nisi ut aliquip ex ea commodo consequat.</p>
  <svg class="arrows" width="24" height="16" viewBox="0 0 24 16"><path d="M8 2L2 8l6 6M16 2l6 6-6 6" fill="none" stroke="#fff" stroke-width="2"/></svg>
</div>

<h2 class="abs section-title" style="left:54px;top:374px;width:377px">Recent Posts</h2>
<h2 class="abs section-title" style="left:448px;top:374px;width:168px">Search</h2>

<article class="abs post" style="top:409px">
  <div class="date">23<br>Nov</div>
  <div class="shares"><i><b></b></i><i><b></b></i><i><b></b></i><i><b></b></i></div>
  <div class="photo" role="img" aria-label="Woman walking down a road toward a bright cross in the sky" style="background:linear-gradient(180deg,#7fb0de,#dfe9f2 55%,#bfc3c5)"></div>
  <div class="card">
    <h3>Nemo enim ipsam voluptatem quia volup</h3>
    <div class="meta">April 23 2015 &nbsp; / &nbsp; 2 comments</div>
    <p>Lorem ipsum dolor sit amet, consectetur adipiscing elit, sed do eiusmod tempor incididunt ut labore et dolore magna aliqua. Ut enim ad minim veniam, quis</p>
    <span class="more">READ MORE</span>
  </div>
</article>

<article class="abs post" style="top:533px">
  <div class="date">23<br>Nov</div>
  <div class="shares"><i><b></b></i><i><b></b></i><i><b></b></i><i><b></b></i></div>
  <div class="photo" role="img" aria-label="Two women praying together" style="background:linear-gradient(90deg,#c99b7c,#eadfd6 55%,#c7cfd6)"></div>
  <div class="card">
    <h3>Nemo enim ipsam voluptatem quia volup</h3>
    <div class="meta">April 23 2015 &nbsp; / &nbsp; 2 comments</div>
    <p>Lorem ipsum dolor sit amet, consectetur adipiscing elit, sed do eiusmod tempor incididunt ut labore et dolore magna aliqua. Ut enim ad minim veniam, quis</p>
    <span class="more">READ MORE</span>
  </div>
</article>

<form class="abs search-panel">
  <div class="field">Name *</div>
  <div class="field">Phone Number *</div>
  <div class="field">Phone No *</div>
  <div class="field">Message*</div>
  <span class="btn">Submit Now</span>
</form>

<div class="abs subscribe">
  <svg class="abs" style="left:14px;top:10px" width="22" height="24" viewBox="0 0 22 24"><path d="M2 10l9-8 9 8v12H2z" fill="#fff" stroke="#bbb"/><path d="M2 10l9 7 9-7" fill="none" stroke="#bbb"/><rect x="6" y="5" width="10" height="7" fill="#fff" stroke="#ccc"/></svg>
  <h4>Subscribe to<br>Follow</h4>
  <div class="email">Email Address</div>
  <span class="btn">Sign Up</span>
</div>

<h2 class="abs section-title" style="left:54px;top:671px;width:562px">Relevant Posts</h2>

<article class="abs rel" style="left:55px">
  <div class="photo" role="img" aria-label="Person standing on a mountain above the clouds" style="background:linear-gradient(180deg,#86a9c6,#e8e4dc 55%,#5b5247)"></div>
  <div class="date">Nov 18, 2015</div>
  <p>Nullas tempus neque massa id mollis neque fesrli convallis ut. Morbi estr velit tincidunt quis felis etv</p>
  <div class="loc"><svg width="6" height="8" viewBox="0 0 12 16"><path d="M6 0a6 6 0 00-6 6c0 4.5 6 10 6 10s6-5.5 6-10a6 6 0 00-6-6zm0 8.5A2.5 2.5 0 116 3.5a2.5 2.5 0 010 5z" fill="#555"/></svg>8, Meadow Lane, Clearwater,<span class="go">&#8600;</span></div>
</article>
<article class="abs rel" style="left:199px">
  <div class="photo" role="img" aria-label="Open hands raised toward a bright sky" style="background:linear-gradient(180deg,#9fbcd6,#eef1f3 50%,#b59c88)"></div>
  <div class="date">Nov 18, 2015</div>
  <p>Nullas tempus neque massa id mollis neque fesrli convallis ut. Morbi estr velit tincidunt quis felis etv</p>
  <div class="loc"><svg width="6" height="8" viewBox="0 0 12 16"><path d="M6 0a6 6 0 00-6 6c0 4.5 6 10 6 10s6-5.5 6-10a6 6 0 00-6-6zm0 8.5A2.5 2.5 0 116 3.5a2.5 2.5 0 010 5z" fill="#555"/></svg>8, Meadow Lane, Clearwater,<span class="go">&#8600;</span></div>
</article>
<article class="abs rel" style="left:343px">
  <div class="photo" role="img" aria-label="Child in a yellow sweater praying" style="background:linear-gradient(90deg,#4a3a2e,#e3c33c 50%,#d8d2c8)"></div>
  <div class="date">Nov 18, 2015</div>
  <p>Nullas tempus neque massa id mollis neque fesrli convallis ut. Morbi estr velit tincidunt quis felis etv</p>
  <div class="loc"><svg width="6" height="8" viewBox="0 0 12 16"><path d="M6 0a6 6 0 00-6 6c0 4.5 6 10 6 10s6-5.5 6-10a6 6 0 00-6-6zm0 8.5A2.5 2.5 0 116 3.5a2.5 2.5 0 010 5z" fill="#555"/></svg>8, Meadow Lane, Clearwater,<span class="go">&#8600;</span></div>
</article>
<article class="abs rel" style="left:487px">
  <div class="photo" role="img" aria-label="Person with arms raised at sunset on a hilltop" style="background:linear-gradient(180deg,#5d6b80,#f2c06a 55%,#7a2a14)"></div>
  <div class="date">Nov 18, 2015</div>
  <p>Nullas tempus neque massa id mollis neque fesrli convallis ut. Morbi estr velit tincidunt quis felis etv</p>
  <div class="loc"><svg width="6" height="8" viewBox="0 0 12 16"><path d="M6 0a6 6 0 00-6 6c0 4.5 6 10 6 10s6-5.5 6-10a6 6 0 00-6-6zm0 8.5A2.5 2.5 0 116 3.5a2.5 2.5 0 010 5z" fill="#555"/></svg>8, Meadow Lane, Clearwater,<span class="go">&#8600;</span></div>
</article>

<section class="abs archive">
  <h2>ARCHIVE POSTS</h2>
  <div class="item">
    <h3>Nemo enim ipsam voluptatem quia</h3>
    <div class="meta">2015 &nbsp;/&nbsp; <small>0 COMMENTS</small></div>
    <p>Lorem ipsum dolor sit amet, consectetur adipiscing elit, sed do eiusmod tempor incididunt ut labore et dolore magna aliqua. Ut enim ad minim</p>
  </div>
  <div class="item" style="border-bottom:none">
    <h3>Nemo enim ipsam voluptatem quia</h3>
    <div class="meta">2015 &nbsp;/&nbsp; <small>0 COMMENTS</small></div>
    <p>Lorem ipsum dolor sit amet, consectetur adipiscing elit, sed do eiusmod tempor incididunt ut labore</p>
  </div>
</section>

<section class="abs video">
  <div class="photo" role="img" aria-label="Hands holding prayer beads"></div>
  <svg class="play" width="24" height="24" viewBox="0 0 24 24"><circle cx="12" cy="12" r="11" fill="rgba(255,255,255,.55)" stroke="#333" stroke-width="1.5"/><path d="M9.5 7.5l7 4.5-7 4.5z" fill="#333"/></svg>
  <h4>e-cart capabilities</h4>
  <p>Lorem ipsum dolor sit amet, consectetur adipiscing elit, sed do eiusmod tempor incididunt ut labore et dolore magna aliqua. Ut enim ad minim</p>
</section>

<section class="abs feed">
  <div class="head">Chirp Updates</div>
  <span class="badge"></span>
  <div class="scroll"><i></i></div>
  <div class="tweet">
    <span class="av"></span>
    <div class="who">My Pebble Porch Path<small>@My Pebble Porch Path</small></div>
    <p>Lorem ipsum dolor sit amet, consectetur ading elit, sed do eiusmod tempor incididunt ut labore et dolore magna aliqua.</p>
  </div>
  <div class="tweet" style="border-bottom:none">
    <span class="av"></span>
    <div class="who">My Pebble Porch Path<small>@My Pebble Porch Path</small></div>
    <p>Lorem ipsum dolor sit amet, consectetur ading elit, sed do eiusmod tempor incididunt ut labore et dolore magna aliqua.</p>
  </div>
</section>

<footer class="abs footer">
  <div class="icons"><span></span><span></span><span></span><span></span><span></span></div>
  <nav>Home &nbsp;/ &nbsp;Contact &nbsp;/ &nbsp;Topics &nbsp;/ &nbsp;e-cart capabilities &nbsp;/ &nbsp;Discussion &nbsp;/ &nbsp;Videos Links</nav>
  <small>Copyright @ 2014 - 2015. &nbsp;My Pebble Porch Path. All Rights Reserved.</small>
</footer>

</body>
</html>
```